Switch Kit - Banking Flyer

We want a design for an 8.5x11" flyer that matches the look of our website (www.morvellcommercebank.com). Outline is attached, but please feel free to include images/pictures/graphics that you think makes this easy to understand. The goal is to hand this flyer to a potential customer to get them to understand the information easily and quickly.

```html
<!DOCTYPE html>
<html lang="en">
<head>
<meta charset="utf-8">
<title>Switch Kit – Morvell Commerce Bank Flyer</title>
<link rel="stylesheet" href="https://fonts.googleapis.com/css2?family=Oswald:wght@600;700&family=Arimo:ital,wght@0,400;0,700;1,400;1,500&display=swap">
<style>
  :root {
    --navy: #3a4a66;
    --gold: #a9762e;
    --charcoal: #3f3f41;
    --ink: #2f2f31;
    --rule: #8a8a8a;
    --paper: #ffffff;
    --backdrop: #d0d0d0;
    --photo-sky: #3f8a93;
    --photo-stone: #c8987a;
  }
  * { box-sizing: border-box; margin: 0; padding: 0; }
  html, body { width: 1100px; height: 1200px; overflow: hidden; }
  body {
    background: var(--backdrop);
    font-family: "Arimo", Arial, sans-serif;
    color: var(--ink);
    position: relative;
  }
  .flyer {
    position: absolute;
    left: 110px; top: 32px;
    width: 880px; height: 1136px;
    background: var(--paper);
    overflow: hidden;
  }
  .hero-photo {
    position: absolute; left: 0; top: 0;
    width: 880px; height: 268px;
    background:
      linear-gradient(180deg, var(--photo-sky) 0%, #2f6f78 40%, var(--photo-stone) 52%, #b97a5e 80%, #3e6c6e 100%);
  }
  .headline {
    position: absolute; left: 64px; top: 322px;
    font-family: "Oswald", "Arial Narrow", sans-serif;
    font-weight: 700;
    font-size: 98px;
    line-height: 100px;
    letter-spacing: -1px;
    text-transform: uppercase;
    background: linear-gradient(90deg, var(--navy) 0%, #5a5352 35%, var(--gold) 75%, var(--gold) 100%);
    -webkit-background-clip: text;
    background-clip: text;
    color: transparent;
    width: 720px;
  }
  .intro {
    position: absolute; left: 67px; top: 540px;
    width: 650px;
    font-style: italic;
    font-weight: 500;
    font-size: 16.5px;
    line-height: 21.5px;
    color: var(--ink);
  }
  .steps {
    position: absolute; left: 0; top: 630px;
    width: 880px; height: 360px;
    display: grid;
    grid-template-columns: 301px 291px 288px;
  }
  .step {
    text-align: center;
    padding-top: 16px;
    position: relative;
  }
  .step + .step { border-left: 1.5px solid var(--rule); }
  .step-number {
    font-size: 19px;
    color: var(--charcoal);
    letter-spacing: 0.3px;
  }
  .step-icon {
    width: 62px; height: 62px;
    margin: 14px auto 0;
    border-radius: 50%;
    display: flex; align-items: center; justify-content: center;
  }
  .step-icon--gold { background: var(--gold); }
  .step-icon--navy { background: var(--navy); }
  .step-icon--dark { background: var(--charcoal); }
  .step-title {
    margin-top: 18px;
    font-size: 14.5px;
    line-height: 16px;
    color: var(--ink);
    min-height: 52px;
  }
  .step-body {
    font-size: 11px;
    line-height: 14px;
    color: #444;
    margin: 6px auto 0;
  }
  .step-body p + p { margin-top: 14px; }
  .step:nth-child(1) .step-body { width: 170px; }
  .step:nth-child(2) .step-body { width: 220px; }
  .step:nth-child(3) .step-body { width: 170px; }
  .step:nth-child(1) { padding-left: 86px; padding-right: 0; }
  .step:nth-child(1) .step-number,
  .step:nth-child(1) .step-icon,
  .step:nth-child(1) .step-title,
  .step:nth-child(1) .step-body { position: relative; left: -70px; }
  .footer-band {
    position: absolute; left: 0; top: 1010px;
    width: 880px; height: 113px;
  }
  .footer-band svg { position: absolute; inset: 0; }
  .brand-name {
    position: absolute; left: 64px; top: 42px;
    font-size: 26px;
    font-weight: 700;
    color: #ffffff;
    letter-spacing: 1px;
  }
  .contact {
    position: absolute; left: 484px; top: 16px;
    color: #ffffff;
  }
  .contact-phone {
    font-family: "Arimo", Arial, sans-serif;
    font-weight: 700;
    font-size: 50px;
    line-height: 56px;
    letter-spacing: -0.5px;
  }
  .contact-web {
    font-weight: 700;
    font-size: 19.5px;
    margin-top: 2px;
    padding-left: 2px;
  }
</style>
</head>
<body>
  <main class="flyer">
    <div class="hero-photo" role="img" aria-label="Photograph of the bank's stone office building with tall reflective windows and the bank name mounted on the facade"></div>

    <h1 class="headline">Switching as<br>easy as 1-2-3 !!!</h1>

    <p class="intro">One of the main reasons people don’t switch banks is that it can be a hassle. At Morvell Commerce Bank we make it easy. We value your time and with our efficient three step process, switching banks has never been easier.</p>

    <section class="steps">
      <article class="step">
        <h2 class="step-number">STEP 01</h2>
        <div class="step-icon step-icon--gold">
          <svg width="34" height="34" viewBox="0 0 34 34" fill="none" stroke="#fff" stroke-width="2.4">
            <circle cx="17" cy="11" r="6.5"/>
            <path d="M5 31v-3a7 7 0 0 1 7-7h10a7 7 0 0 1 7 7v3z" stroke-linejoin="round"/>
          </svg>
        </div>
        <h3 class="step-title">Open a Morvell<br>Commerce Bank Account</h3>
        <div class="step-body">
          <p>Stop by our branch and visit with our knowledgeable team to open your new account. We will be happy to assist you in choosing the right account for your banking needs.</p>
        </div>
      </article>

      <article class="step">
        <h2 class="step-number">STEP 02</h2>
        <div class="step-icon step-icon--navy">
          <svg width="36" height="36" viewBox="0 0 36 36" fill="none" stroke="#fff" stroke-width="1.8" stroke-linejoin="round">
            <rect x="4" y="5" width="20" height="15" rx="2"/>
            <line x1="4" y1="9.5" x2="24" y2="9.5"/>
            <rect x="13" y="16" width="19" height="14" rx="2" fill="#3a4a66"/>
            <line x1="13" y1="20.5" x2="32" y2="20.5"/>
            <path d="M9 24v5h3"/>
          </svg>
        </div>
        <h3 class="step-title">Stop using your old account<br>and redirect your automatic<br>payments and direct deposits</h3>
        <div class="step-body">
          <p>It is important to remember to keep your old account open to ensure all your outstanding checks, deposits, and automatic withdrawals have cleared.</p>
          <p>We will provide you with a Payments Checklist to help you determine the companies you may need to notify of your account change so they can redirect any deposits or automatic withdrawals.</p>
        </div>
      </article>

      <article class="step">
        <h2 class="step-number">STEP 03</h2>
        <div class="step-icon step-icon--dark">
          <svg width="30" height="30" viewBox="0 0 30 30" stroke="#fff" stroke-width="5" stroke-linecap="square">
            <line x1="7" y1="7" x2="23" y2="23"/>
            <line x1="23" y1="7" x2="7" y2="23"/>
          </svg>
        </div>
        <h3 class="step-title">Close your<br>old account</h3>
        <div class="step-body">
          <p>Now you are ready to switch. We will even provide an Account Closure Authorization form to close your old account. Any remaining account balance will be transferred to your Morvell Commerce Bank account.</p>
        </div>
      </article>
    </section>

    <footer class="footer-band">
      <svg width="880" height="113" viewBox="0 0 880 113">
        <rect width="880" height="113" fill="var(--navy)"/>
        <polygon points="0,0 468,0 432,113 0,113" fill="var(--gold)"/>
      </svg>
      <div class="brand-name">Morvell Commerce Bank</div>
      <div class="contact">
        <div class="contact-phone">480.555.0142</div>
        <div class="contact-web">www.morvellcommercebank.com</div>
      </div>
    </footer>
  </main>
</body>
</html>
```